Business Card Design

New business card design

Target Market(s)

Residential & Commercial Property Managers

Industry/Entity Type

Plumbing Services

Contact Information for Business Card

Name - Rowan Keddle, title - Director, Phone Number - 0431 286 517, email - rowan@tbk-plumbing.com.au, Company ABN - 73 215 904 386,

Font styles to use
Sans Serif

Colors
0054AA
0677BA
7BADD7
CADEEF
E8F1F8

```html
<!DOCTYPE html>
<html lang="en">
<head>
<meta charset="utf-8">
<title>TBK Plumbing Services – Business Card</title>
<link href="https://fonts.googleapis.com/css2?family=Arimo:wght@400;700&display=swap" rel="stylesheet">
<style>
  :root{
    --stage:#3d3d3d;
    --card-dark:#1e242b;
    --card-light:#ffffff;
    --accent:#1aa3e8;
    --ink:#1e242b;
    --text-light:#ffffff;
    --text-soft:#d7dde3;
    --pattern-a:#2a3540;
    --pattern-b:#141a20;
  }
  *{margin:0;padding:0;box-sizing:border-box}
  html,body{width:1200px;height:803px;overflow:hidden}
  body{
    background:var(--stage);
    font-family:"Arimo", Arial, sans-serif;
    position:relative;
  }
  .card{
    position:absolute;
    top:252px;
    width:530px;
    height:300px;
    border-radius:22px;
    overflow:hidden;
    box-shadow:0 18px 40px rgba(0,0,0,.45);
  }
  .card--front{left:45px;background:var(--card-dark)}
  .card--back{left:625px}
  .front-shape{position:absolute;inset:0;width:100%;height:100%}
  .brand{
    position:absolute;
    left:24px;
    top:182px;
    color:var(--ink);
    font-size:17px;
    font-weight:400;
    letter-spacing:.3px;
    display:flex;
    align-items:center;
    gap:9px;
    white-space:nowrap;
  }
  .brand__dot{width:11px;height:11px;border-radius:50%;background:var(--accent)}
  .contact{
    position:absolute;
    right:30px;
    top:38px;
    text-align:right;
    color:var(--text-light);
  }
  .contact__name{font-size:24px;font-weight:700;letter-spacing:.3px}
  .contact__title{font-size:13px;color:var(--text-soft);margin-top:3px}
  .contact__lines{margin-top:28px;font-size:13.5px;line-height:1.65;color:var(--text-soft)}
  .contact__line{display:flex;justify-content:flex-end;align-items:center;gap:8px;white-space:nowrap}
  .contact__line svg{width:12px;height:12px;fill:var(--text-light)}
  .contact__abn{margin-top:10px}
  .back-pattern{
    position:absolute;inset:0;
    background:linear-gradient(120deg,var(--pattern-b) 0%,var(--card-dark) 45%,var(--pattern-a) 100%);
  }
</style>
</head>
<body>
  <section class="card card--front">
    <svg class="front-shape" viewBox="0 0 530 300" preserveAspectRatio="none">
      <path d="M0,0 L130,0 C225,40 275,170 268,300 L0,300 Z" fill="var(--card-light)"/>
      <path d="M130,0 C225,40 275,170 268,300" fill="none" stroke="var(--accent)" stroke-width="5" transform="translate(6,-3)"/>
      <path d="M130,0 C225,40 275,170 268,300" fill="none" stroke="var(--ink)" stroke-width="2"/>
    </svg>
    <div class="brand"><span class="brand__dot"></span>TBK Plumbing Services</div>
    <div class="contact">
      <div class="contact__name">Rowan Keddle</div>
      <div class="contact__title">Director</div>
      <div class="contact__lines">
        <div class="contact__line">0431 286 517
          <svg viewBox="0 0 24 24"><path d="M6.6 10.8a15.1 15.1 0 0 0 6.6 6.6l2.2-2.2a1 1 0 0 1 1-.25 11.4 11.4 0 0 0 3.6.6 1 1 0 0 1 1 1V20a1 1 0 0 1-1 1A17 17 0 0 1 3 4a1 1 0 0 1 1-1h3.5a1 1 0 0 1 1 1c0 1.25.2 2.450.57 3.57a1 1 0 0 1-.25 1z"/></svg>
        </div>
        <div class="contact__line">rowan@tbk-plumbing.com.au
          <svg viewBox="0 0 24 24"><path d="M2 5h20v14H2z M2 5l10 8 10-8" fill="var(--text-light)" stroke="var(--card-dark)" stroke-width="1.5"/></svg>
        </div>
        <div class="contact__line contact__abn">ABN - 73 215 904 386</div>
      </div>
    </div>
  </section>

  <section class="card card--back">
    <div class="back-pattern" role="img" aria-label="Repeating water droplet pattern on dark background"></div>
  </section>
</body>
</html>
```